Retainer Care Instructions

Please make this PDF - more modern and easy to read for patients. Our demographic is predominately adolescents. All the information is important and text needs to remain relatively the same - can be simplified. Here is a link to care instructions that look nice https://www.brightlane-grins.com/resources

Target Market(s)

Parents and Children

Industry/Entity Type

Orthodontics

Colors
0054AA
0677BA
7BADD7
CADEEF
E8F1F8

Requirements
Must have
• Simple and clear
Nice to have
• Add graphics and images to look more modern
Should not have
• Graphics to demonstrate

```html
<!DOCTYPE html>
<html lang="en">
<head>
<meta charset="utf-8">
<title>The Braces Are Off – It's Retainer Time!</title>
<link href="https://fonts.googleapis.com/css2?family=Roboto+Condensed:wght@400;700&family=Ubuntu:wght@500;700&display=swap" rel="stylesheet">
<style>
  :root {
    --brand-blue: #0a97de;
    --ink: #2a2a2a;
    --body-ink: #333333;
    --rule: #dcdcdc;
    --band: #ade4fc;
    --icon-fill: #d6f0fc;
    --warning-pink: #f1456a;
    --warning-yellow: #ffe600;
    --white: #ffffff;
  }
  * { margin: 0; padding: 0; box-sizing: border-box; }
  html, body { width: 849px; height: 1200px; overflow: hidden; background: var(--white); }
  .sheet {
    position: relative; width: 849px; height: 1200px; overflow: hidden;
    background: var(--white); font-family: "Roboto Condensed", "Arial Narrow", sans-serif; color: var(--body-ink);
  }
  .abs { position: absolute; }

  /* Header */
  .brand { left: 40px; top: 60px; width: 170px; }
  .brand-mark { display: block; width: 60px; height: 60px; border-radius: 50%; background: var(--brand-blue); margin: 0 0 10px 50px; }
  .brand-name { font-family: "Ubuntu", sans-serif; font-weight: 500; font-size: 21px; line-height: 1.1; color: var(--brand-blue); text-align: center; }
  .headline {
    left: 232px; top: 44px; width: 560px; text-align: center;
    font-family: "Ubuntu", sans-serif; font-weight: 700; font-size: 61px; line-height: 54px;
    color: var(--brand-blue); letter-spacing: -0.5px;
  }
  .rule { height: 3px; background: var(--rule); }
  .rule-top { left: 44px; top: 185px; width: 761px; }

  /* Care list */
  .section-title {
    font-family: "Ubuntu", sans-serif; font-weight: 700; font-size: 30px; color: var(--ink);
    text-align: center; letter-spacing: 0.3px;
  }
  .care-title { left: 0; top: 226px; width: 849px; }
  .care-item { display: flex; align-items: flex-start; }
  .care-num { font-family: "Ubuntu", sans-serif; font-weight: 700; font-size: 19px; color: var(--ink); width: 30px; padding-top: 4px; }
  .care-icon { width: 70px; height: 72px; border-radius: 10px; background: var(--icon-fill); flex: none; margin-right: 36px; }
  .care-text { font-size: 16.6px; line-height: 22px; color: var(--body-ink); }
  .care-text b { font-weight: 700; color: var(--ink); }
  .col-left { left: 22px; }
  .col-right { left: 441px; }
  .col-left .care-text { width: 290px; }
  .col-right .care-text { width: 260px; }
  .row-1 { top: 290px; }
  .row-2 { top: 402px; }
  .row-3 { top: 513px; }
  .rule-1 { left: 32px; top: 377px; width: 785px; height: 2px; }
  .rule-2 { left: 32px; top: 490px; width: 785px; height: 2px; }
  .rule-3 { left: 218px; top: 602px; width: 413px; height: 2px; }
  .row-4 { left: 227px; top: 624px; }
  .row-4 .care-num { width: 33px; padding-top: 8px; }
  .row-4 .care-icon { width: 66px; height: 70px; margin-right: 24px; }
  .row-4 .care-text { width: 280px; }

  /* Cleaning band */
  .clean-tab { left: 199px; top: 735px; width: 451px; height: 50px; background: var(--band); border-radius: 20px 20px 0 0; }
  .clean-band { left: 0; top: 771px; width: 849px; height: 429px; background: var(--band); }
  .clean-title { left: 199px; top: 742px; width: 451px; font-size: 28px; }
  .clean-illus { border-radius: 12px; background: rgba(255,255,255,0.45); }
  .illus-soak { left: 42px; top: 800px; width: 110px; height: 124px; }
  .illus-rinse { left: 476px; top: 793px; width: 124px; height: 130px; }
  .clean-text { font-size: 18px; line-height: 23.5px; color: var(--body-ink); }
  .clean-text b { font-weight: 700; color: var(--ink); }
  .step-soak { left: 165px; top: 821px; width: 240px; }
  .step-rinse { left: 620px; top: 821px; width: 200px; }
  .step-arrow { left: 417px; top: 845px; width: 26px; height: 24px; }

  /* Warning card */
  .warning-card { left: 44px; top: 975px; width: 761px; height: 180px; background: var(--white); border-radius: 26px; }
  .warning-icon { left: 290px; top: 986px; width: 56px; height: 42px; }
  .warning-label { left: 362px; top: 992px; font-family: "Ubuntu", sans-serif; font-weight: 700; font-size: 25px; color: var(--warning-pink); letter-spacing: 0.5px; }
  .warning-list { left: 86px; top: 1038px; width: 700px; list-style: none; font-size: 16.8px; line-height: 23px; color: var(--body-ink); }
  .warning-list b { font-weight: 700; color: var(--ink); }
  .warning-list .indent { padding-left: 19px; }
</style>
</head>
<body>
<main class="sheet">

  <header>
    <div class="abs brand">
      <span class="brand-mark" aria-hidden="true"></span>
      <div class="brand-name">Brightlane Orthodontics</div>
    </div>
    <h1 class="abs headline">The Braces Are Off<br>It's Retainer Time!</h1>
  </header>
  <div class="abs rule rule-top"></div>

  <section>
    <h2 class="abs section-title care-title">HOW TO CARE FOR RETAINERS:</h2>

    <div class="abs care-item col-left row-1">
      <span class="care-num">1.</span>
      <div class="care-icon" role="img" aria-label="Line icon of an orthodontist beside a tooth"></div>
      <p class="care-text"><b>Wear your retainer as instructed:</b> Always wear your retainer as instructed by your orthodontist</p>
    </div>
    <div class="abs care-item col-right row-1">
      <span class="care-num">2.</span>
      <div class="care-icon" role="img" aria-label="Line icon of a drink, burger and football"></div>
      <p class="care-text"><b>Remove retainer during meals and sports:</b> Take out your retainer when eating and playing sports.</p>
    </div>
    <div class="abs rule rule-1"></div>

    <div class="abs care-item col-left row-2">
      <span class="care-num">3.</span>
      <div class="care-icon" role="img" aria-label="Line icon of a wallet with a dollar coin"></div>
      <p class="care-text"><b>Don't lose your retainer:</b> Be careful not to lose your retainer, as replacement will incur an additional fee of $300 per retainer.</p>
    </div>
    <div class="abs care-item col-right row-2">
      <span class="care-num">4.</span>
      <div class="care-icon" role="img" aria-label="Line icon of a retainer inside a storage container"></div>
      <p class="care-text"><b>Store retainer properly:</b> Always store your retainer in the provided container.</p>
    </div>
    <div class="abs rule rule-2"></div>

    <div class="abs care-item col-left row-3">
      <span class="care-num">5.</span>
      <div class="care-icon" role="img" aria-label="Line icon of a cleaner bottle and toothbrush"></div>
      <p class="care-text"><b>Clean your retainer regularly:</b> Use a toothbrush and retainer cleaner (such as FreshSoak) to clean your retainer.</p>
    </div>
    <div class="abs care-item col-right row-3">
      <span class="care-num">6.</span>
      <div class="care-icon" role="img" aria-label="Line icon of a retainer with a width arrow"></div>
      <p class="care-text"><b>Check retainer fit:</b> If your retainer doesn't fit properly, call us to arrange for it to be checked and adjusted.</p>
    </div>
    <div class="abs rule rule-3"></div>

    <div class="abs care-item row-4">
      <span class="care-num">7.</span>
      <div class="care-icon" role="img" aria-label="Line icon of an appointment calendar with a clock"></div>
      <p class="care-text"><b>Attend retainer check appointments:</b> Regularly attend retainer check appoint-ments to have your retainer tightened.</p>
    </div>
  </section>

  <section>
    <div class="abs clean-tab"></div>
    <div class="abs clean-band"></div>
    <h2 class="abs section-title clean-title">HOW TO CLEAN A RETAINER:</h2>

    <div class="abs clean-illus illus-soak" role="img" aria-label="Illustration of a retainer soaking in a bowl of water with a cleaning tablet"></div>
    <p class="abs clean-text step-soak">1. <b>Use cleaning tablets:</b> Drop one tablet into warm water, place retainer in solution, and leave for 10-15 minutes.</p>

    <svg class="abs step-arrow" viewBox="0 0 26 24" aria-hidden="true">
      <path d="M3 3 L11 12 L3 21 M13 3 L21 12 L13 21" fill="none" stroke="#1a1a1a" stroke-width="3" stroke-linecap="round" stroke-linejoin="round"/>
    </svg>

    <div class="abs clean-illus illus-rinse" role="img" aria-label="Illustration of a retainer being rinsed under a running tap"></div>
    <p class="abs clean-text step-rinse">2. <b>Rinse thoroughly:</b> Rinse retainer with running water after cleaning.</p>

    <div class="abs warning-card"></div>
    <svg class="abs warning-icon" viewBox="0 0 56 42" aria-hidden="true">
      <path d="M28 2 L54 40 L2 40 Z" fill="var(--warning-yellow)" stroke="#1a1a1a" stroke-width="2.5" stroke-linejoin="round"/>
      <path d="M28 13 L28 28" stroke="#1a1a1a" stroke-width="4" stroke-linecap="round"/>
      <circle cx="28" cy="34" r="2.4" fill="#1a1a1a"/>
    </svg>
    <div class="abs warning-label">WARNING:</div>
    <ul class="abs warning-list">
      <li><b>1. Don't ingest cleaning tablets:</b> Do not place tablets in mouth or use to clean natural teeth.</li>
      <li><b>2. Keep out of reach of children:</b> Keep cleaning tablets out of reach of children.</li>
      <li><b>3. Seek help in case of accidental ingestion:</b> If accidentally ingested, seek professional assistance or</li>
      <li class="indent">contact poison center immediately.</li>
    </ul>
  </section>

</main>
</body>
</html>
```